An awsome Vento salt flyer!

We need a professional looking flyer for our mineralsalt product. Named "Vento salt" coming from Maras Peru from the "Terrazales". I have an example but it's not professional looking yet. I hope you can make an amazing flyer for us! valecrestafoods.com is our webpage.
Target Market(s)
Bio shoppers, natural food lovers, healty food lovers,
Industry/Entity Type
Food Store
Requirements
Nice to have
- We would like to have a really nice professionally looking flyer. For the common flyer sizes like DL and A5. I uploaded some bag pictures too. They will be improved soon but its nice to show the product as well. The pink and yellow colors we use in the logo and package would be nice as well.

```html
<!DOCTYPE html>
<html lang="nl">
<head>
<meta charset="utf-8">
<title>Vento Zout – flyer</title>
<link rel="stylesheet" href="https://fonts.googleapis.com/css2?family=Tinos:wght@400;700&family=Noto+Serif:wght@700&family=PT+Sans:wght@400;700&display=swap">
<style>
  :root{
    --pink:#e52a8a;
    --pink-deep:#c91f74;
    --pink-soft:#f8b7d6;
    --yellow:#f9c52a;
    --yellow-light:#fdf24e;
    --ink:#2a2320;
    --white:#ffffff;
    --page:#ece7df;
  }
  *{box-sizing:border-box;margin:0;padding:0}
  html,body{width:1200px;height:1020px;overflow:hidden;background:var(--page)}
  .canvas{position:relative;width:1200px;height:1020px}
  .flyer{position:absolute;top:136px;width:374px;height:748px;overflow:hidden;
    box-shadow:0 4px 10px rgba(0,0,0,.25)}
  .flyer--front{left:198px;background:radial-gradient(ellipse at 60% 65%,var(--yellow-light) 0%,var(--yellow) 85%)}
  .flyer--back{left:626px;background:var(--yellow)}
  .shapes{position:absolute;inset:0}

  .brand{position:absolute;top:20px;left:0;width:100%;text-align:center;font-family:"Tinos",serif;
    color:var(--pink);font-size:30px;line-height:34px;font-weight:400;letter-spacing:.3px}
  .tagline{position:absolute;top:56px;left:0;width:100%;text-align:center;font-family:"Tinos",serif;
    font-size:15px;line-height:18px;color:var(--ink)}

  .product-bag{position:absolute;left:36px;top:355px;width:114px;height:240px;border-radius:8px 8px 4px 4px;
    background:linear-gradient(160deg,#f25aa6 0%,var(--pink) 45%,var(--pink-deep) 100%);
    box-shadow:2px 3px 6px rgba(0,0,0,.3)}

  .claim{position:absolute;right:22px;top:480px;text-align:right;font-family:"Noto Serif",serif;
    font-weight:700;color:var(--pink);font-size:13.5px;line-height:16px}
  .claim-minerals{position:absolute;right:22px;top:532px;text-align:right;font-family:"PT Sans",sans-serif;
    font-size:12.5px;line-height:13.5px;color:var(--pink);font-weight:700}
  .claim-list{position:absolute;right:22px;top:562px;text-align:right;font-family:"PT Sans",sans-serif;
    font-size:12.5px;line-height:14.5px;color:var(--ink)}

  .benefits-title{position:absolute;left:27px;top:602px;width:228px;height:28px;border-radius:14px;
    background:var(--pink);color:var(--white);font-family:"PT Sans",sans-serif;font-weight:700;
    font-size:14.5px;line-height:24px;text-align:center;border:2px solid var(--pink-soft)}
  .benefits{position:absolute;left:30px;top:640px;list-style:none;font-family:"PT Sans",sans-serif;
    font-size:12.5px;line-height:16.4px;color:var(--ink)}
  .benefits li{position:relative;padding-left:18px;white-space:nowrap}
  .benefits li::before{content:"";position:absolute;left:3px;top:3px;width:4px;height:8px;
    border:solid var(--pink);border-width:0 2px 2px 0;transform:rotate(40deg)}

  .info{position:absolute;left:33px;top:174px;width:318px;font-family:"PT Sans",sans-serif;color:var(--ink)}
  .info h2{font-size:14px;font-weight:700;color:var(--pink);margin-top:7px;line-height:18px}
  .info h2:first-child{margin-top:0}
  .info p{font-size:10.5px;line-height:15px;white-space:nowrap}
</style>
</head>
<body>
<div class="canvas">

  <section class="flyer flyer--front">
    <svg class="shapes" width="374" height="748" viewBox="0 0 374 748">
      <defs>
        <linearGradient id="terraces" x1="0" y1="0" x2="0" y2="1">
          <stop offset="0" stop-color="#8d6550"/>
          <stop offset=".35" stop-color="#cdb9a6"/>
          <stop offset=".7" stop-color="#e9e2d6"/>
          <stop offset="1" stop-color="#d8c8b8"/>
        </linearGradient>
        <linearGradient id="worker" x1="0" y1="0" x2="1" y2="1">
          <stop offset="0" stop-color="#6f7a86"/>
          <stop offset="1" stop-color="#c9c3bd"/>
        </linearGradient>
        <linearGradient id="pools" x1="0" y1="0" x2="1" y2="1">
          <stop offset="0" stop-color="#a9826b"/>
          <stop offset="1" stop-color="#efe7dc"/>
        </linearGradient>
      </defs>
      <path d="M0,150 C120,120 260,86 374,72 L374,90 C260,102 120,138 0,168 Z" fill="var(--pink)"/>
      <path d="M0,168 C120,138 260,102 374,90 L374,392 C250,410 110,440 0,462 Z" fill="url(#terraces)"
            role="img" aria-label="Foto van de zoutterrassen in de vallei met werkers tussen de witte zoutpannen"/>
      <path d="M0,462 C110,440 250,410 374,392 L374,406 C250,424 110,456 0,478 Z" fill="var(--pink)"/>
      <circle cx="96" cy="158" r="54" fill="var(--pink)"/>
      <circle cx="96" cy="158" r="47" fill="url(#worker)" role="img" aria-label="Foto van een zoutwinner aan het werk"/>
      <circle cx="326" cy="680" r="67" fill="var(--pink)"/>
      <circle cx="326" cy="680" r="59" fill="url(#pools)" role="img" aria-label="Foto van witte zoutpannen"/>
    </svg>

    <h1 class="brand">VENTO ZOUT</h1>
    <p class="tagline">Uit de heilige valle de incas</p>

    <div class="product-bag" role="img" aria-label="Productverpakking Vento Zout mineraal keukenzout"></div>

    <p class="claim">Het meest zuivere<br>en volledige<br>Mineraal Keukenzout</p>
    <p class="claim-minerals">Bevat 84<br>mineralen en sporenelmenten</p>
    <p class="claim-list">o.a: calcium, ijzer, zink, magnesium<br>en voldoende jodium (3,5 mg/100gr)</p>

    <div class="benefits-title">Voordelen van het vento zout</div>
    <ul class="benefits">
      <li>Heerlijk van smaak</li>
      <li>Minder natrium</li>
      <li>Afkomsti van een oude schone oceaan</li>
      <li>Natuurlijk proces van winning</li>
      <li>Met de hand geoogst</li>
      <li>100% eerlijk</li>
    </ul>
  </section>

  <section class="flyer flyer--back">
    <svg class="shapes" width="374" height="748" viewBox="0 0 374 748">
      <defs>
        <linearGradient id="saltpile" x1="0" y1="0" x2="0" y2="1">
          <stop offset="0" stop-color="#9a7e6e"/><stop offset="1" stop-color="#f1ece4"/>
        </linearGradient>
        <linearGradient id="basins" x1="0" y1="0" x2="1" y2="1">
          <stop offset="0" stop-color="#c7b3a3"/><stop offset="1" stop-color="#e8ddd0"/>
        </linearGradient>
        <linearGradient id="valley" x1="0" y1="0" x2="0" y2="1">
          <stop offset="0" stop-color="#9fb0bf"/><stop offset=".45" stop-color="#8b6b57"/><stop offset="1" stop-color="#e6dccf"/>
        </linearGradient>
      </defs>
      <path d="M0,0 H374 V22 C260,40 130,100 0,150 Z" fill="var(--pink)"/>
      <path d="M0,150 C130,100 260,40 374,22 L374,34 C260,54 130,114 0,166 Z" fill="var(--white)"/>
      <circle cx="112" cy="118" r="50" fill="var(--pink)"/>
      <circle cx="112" cy="118" r="43" fill="url(#saltpile)" role="img" aria-label="Foto van hopen gewonnen zout"/>
      <circle cx="198" cy="96" r="56" fill="var(--pink)"/>
      <circle cx="198" cy="96" r="49" fill="url(#basins)" role="img" aria-label="Foto van zoutbassins op de berghelling"/>
      <circle cx="290" cy="64" r="60" fill="var(--pink)"/>
      <circle cx="290" cy="64" r="53" fill="url(#valley)" role="img" aria-label="Foto van de vallei met zoutterrassen en bergen"/>
    </svg>

    <div class="info">
      <h2>HERKOMST</h2>
      <p>Het Vento mineraalzout komt uit Maras-cusco in het Andes<br>geberte van peru, vlakbij Machu picchu.Hier was vroeger het<br>Inca rijk, een oud was met het leven met en van de natuur.Het<br>zout komt van een hele oude en schone oceaan wat in vele<br>duizenden jaren omhoog is gedrukt.Dit bijzondere zout wordt<br>gewonnen door de lokale bevolking in een hele mooie en<br>bijzondere locatie op zo'n 3500 meter hoogte wat het ook een<br>heel zuiver zout maakt.</p>
      <h2>NATUURLIJKE BRON</h2>
      <p>Het begint met een natuurlijk warm stroompje vanuit de berg<br>welke vaia kleine riviertjes uitmond in de zoutpontons.Als een<br>ponton is volgestroomd wordt de toevoer dichtgezet en<br>vervolgens verdampt de de zon en wind het vocht eruit en blijft<br>het zout achter.Een heel natuurlijk en duurzaam proces wat al<br>meer dan 2000 jaar zo gaat.</p>
      <h2>MINERALEN</h2>
      <p>Het zout bevat 84 mineralen en sporen elementen<br>waaronder: calcium, ijzer, magnesium en zink.En er zit ook<br>minder natriun in dit zout dan de gebruikelijke zouten wat het<br>ook een verstandige keus maakt.</p>
      <h2>NATUURLIJKE BRON</h2>
      <p>Het begint met een natuurlijk warm stroompje vanuit de berg<br>welke vaia kleine riviertjes uitmond in de zoutpontons.Als een<br>ponton is volgestroomd wordt de toevoer dichtgezet en<br>vervolgens verdampt de de zon en wind het vocht eruit en blijft<br>het zout achter.Een heel natuurlijk en duurzaam proces wat al<br>meer dan 2000 jaar zo gaat.</p>
      <h2>MINERALEN</h2>
      <p>Het zout bevat 84 mineralen en sporen elementen<br>waaronder: calcium, ijzer, magnesium en zink.En er zit ook<br>minder natriun in dit zout dan de gebruikelijke zouten wat het<br>ook een verstandige keus maakt.</p>
    </div>
  </section>

</div>
</body>
</html>
```